Simple Logo Design for Semi-Clear Plastic Frosted Card stock

Create a business card on frosted plastic. compliment existing logo elements with a tree trunk, roots, or seed at the lower half and the full logo both on the front.

Contact information will go on a solid portion of the back of this design since this card stock is semi-transparent.

It is important to consider this plastic card stock medium in your design. I found helpful tips and guides listed at vellaprint-sample.net: be careful to understand ink printed on plastic cards cannot have too much of a consistent print area or risks peeling and fine lines can easily scratch off.
Updates

2" x 3.5" 20PT Clear Plastic Business cards with Round corners Please get info or templates here: https://www.vellaprint-sample.net/product-detail/2-x-35-20pt-clear-plastic-business-cards-with-round-corners

Target Market(s)

Not for profit- religion

Industry/Entity Type

Business

Must include complementary elements to the existing logo

Font styles to use
Decorative

Colors
000000

Requirements
Must have
• Elements of community, nature and oneness. Such as: seed, roots, tree trunk, etc.
• Three lines of space on the back for Name, Title, Phone Number.
Nice to have
• I like a light use of decorative elements
Should not have
• No eyes, from faces or animals.

```html
<!DOCTYPE html>
<html lang="en">
<head>
<meta charset="utf-8">
<title>Steadfast Grove — Business Card</title>
<link rel="stylesheet" href="https://fonts.googleapis.com/css2?family=Roboto+Condensed:wght@400;500&display=swap">
<style>
  :root {
    --page-bg: #e9e6e1;
    --frost: #eef0ee;
    --frost-edge: #d5dad7;
    --panel-deep: #0b3d38;
    --panel-mid: #145a50;
    --vine-green: #2f6e2a;
    --vine-soft: #6f9c5b;
    --brand-green: #2c6a35;
    --contact-light: #e4ece8;
    --contact-muted: #c3d3cc;
  }
  * { margin: 0; padding: 0; box-sizing: border-box; }
  html, body {
    width: 1200px;
    height: 969px;
    overflow: hidden;
    background: var(--page-bg);
  }
  .card {
    position: absolute;
    left: 100px;
    top: 199px;
    width: 1000px;
    height: 571px;
    border-radius: 30px;
    overflow: hidden;
    background: linear-gradient(160deg, #f6f7f6 0%, var(--frost) 55%, #e3e7e5 100%);
    box-shadow: inset 0 0 0 2px var(--frost-edge), 0 10px 30px rgba(0,0,0,0.12);
  }
  .card-art {
    position: absolute;
    inset: 0;
    width: 1000px;
    height: 571px;
  }
  .brand {
    position: absolute;
    left: 60px;
    top: 200px;
    width: 360px;
    display: flex;
    flex-direction: column;
    align-items: center;
    gap: 18px;
  }
  .brand-mark {
    width: 70px;
    height: 70px;
    border-radius: 50%;
    background: var(--brand-green);
  }
  .brand-name {
    font-family: "Roboto Condensed", sans-serif;
    font-weight: 500;
    font-size: 40px;
    letter-spacing: 1px;
    color: var(--brand-green);
    text-transform: uppercase;
    white-space: nowrap;
  }
  .contact {
    position: absolute;
    left: 682px;
    top: 214px;
    font-family: "Roboto Condensed", sans-serif;
    color: var(--contact-light);
  }
  .contact-name {
    font-size: 38px;
    font-weight: 500;
    letter-spacing: 1.5px;
    line-height: 1;
    text-transform: uppercase;
  }
  .contact-title {
    margin-top: 14px;
    font-size: 31px;
    font-weight: 400;
    letter-spacing: 1px;
    line-height: 1;
    text-transform: uppercase;
    color: var(--contact-muted);
  }
  .contact-phone {
    margin-top: 34px;
    font-size: 31px;
    font-weight: 400;
    letter-spacing: 1px;
    line-height: 1;
    color: var(--contact-muted);
  }
</style>
</head>
<body>
  <div class="card">
    <svg class="card-art" viewBox="0 0 1000 571" xmlns="http://www.w3.org/2000/svg">
      <defs>
        <radialGradient id="vine-tone" cx="975" cy="285.5" r="511" gradientUnits="userSpaceOnUse">
          <stop offset="0.64" stop-color="var(--vine-green)" stop-opacity="0.85"/>
          <stop offset="0.85" stop-color="var(--vine-soft)" stop-opacity="0.55"/>
          <stop offset="1" stop-color="var(--vine-soft)" stop-opacity="0.15"/>
        </radialGradient>
        <linearGradient id="panel-tone" x1="0" y1="0" x2="1" y2="1">
          <stop offset="0" stop-color="var(--panel-mid)"/>
          <stop offset="1" stop-color="var(--panel-deep)"/>
        </linearGradient>
      </defs>
      <circle class="vine-ring" cx="975" cy="285.5" r="511" fill="url(#vine-tone)"
              role="img" aria-label="Leafy vine branches curving around the contact panel"/>
      <circle class="contact-panel" cx="975" cy="285.5" r="330" fill="url(#panel-tone)"/>
    </svg>

    <div class="brand">
      <span class="brand-mark"></span>
      <span class="brand-name">Steadfast Grove</span>
    </div>

    <div class="contact">
      <p class="contact-name">Mara Ellison</p>
      <p class="contact-title">President</p>
      <p class="contact-phone">555 0142 7730</p>
    </div>
  </div>
</body>
</html>
```